KDWB Business Card

Looking for a business card design to incorporate our branding. We want to only use the colors listing in the Branding Package (attached).
Updates

Target Market(s)

People who need their phone or device fixed.

Industry/Entity Type

Electronics

Contact Information for Business Card

Please use:

Brightwick Gadget Clinic LLC
4810 E Harlow Ridge Rd
Suite 417
San Antonio, TX 78163

Marcus Delgrove, Store Manager

(210) 555-0147

Requirements
Must have
• Must include the colors that are contained within the Branding Package PDF file.

```html
<!DOCTYPE html>
<html lang="en">
<head>
<meta charset="utf-8">
<title>Brightwick Gadget Clinic – Business Card</title>
<link rel="stylesheet" href="https://fonts.googleapis.com/css2?family=Josefin+Sans:wght@400&family=Open+Sans:wght@400&display=swap">
<style>
  :root {
    --card-orange: #ff5000;
    --text-white: #ffffff;
    --panel-top: #f7f7f7;
    --panel-bottom: #e6e6e6;
    --brand-orange: #f25a0c;
    --page-bg: #ecebe9;
  }
  * { margin: 0; padding: 0; box-sizing: border-box; }
  html, body {
    width: 1200px;
    height: 900px;
    overflow: hidden;
    background: var(--page-bg);
  }
  .card {
    position: absolute;
    left: 120px;
    top: 153px;
    width: 960px;
    height: 594px;
    background: var(--card-orange);
    color: var(--text-white);
    font-family: "Open Sans", Arial, sans-serif;
  }
  .contact-name {
    position: absolute;
    left: 54px;
    top: 74px;
    font-family: "Josefin Sans", "Century Gothic", sans-serif;
    font-size: 35px;
    letter-spacing: 4px;
    text-transform: uppercase;
    line-height: 1;
  }
  .contact-title {
    position: absolute;
    left: 54px;
    top: 117px;
    font-size: 24px;
    line-height: 1.2;
  }
  .contact-phone {
    position: absolute;
    left: 54px;
    top: 171px;
    display: flex;
    align-items: center;
    gap: 10px;
    font-size: 27px;
    line-height: 1.2;
  }
  .contact-phone svg { width: 27px; height: 27px; fill: var(--text-white); }
  .company-address {
    position: absolute;
    left: 54px;
    top: 427px;
    font-size: 24px;
    line-height: 34px;
  }
  .company-name { text-transform: uppercase; }
  .brand-panel {
    position: absolute;
    left: 471px;
    top: 91px;
    width: 430px;
    height: 412px;
    border-radius: 18px;
    background: linear-gradient(180deg, var(--panel-top), var(--panel-bottom));
    display: flex;
    align-items: center;
    justify-content: center;
    gap: 14px;
  }
  .brand-square {
    width: 40px;
    height: 40px;
    background: var(--brand-orange);
    border-radius: 4px;
    flex: none;
  }
  .brand-name {
    font-size: 30px;
    color: var(--brand-orange);
    line-height: 1.1;
  }
</style>
</head>
<body>
  <div class="card">
    <div class="contact-name">Marcus Delgrove</div>
    <div class="contact-title">Store Manager</div>
    <div class="contact-phone">
      <svg viewBox="0 0 24 24" aria-hidden="true"><path d="M6.6 10.8c1.4 2.8 3.8 5.1 6.6 6.6l2.2-2.2c.3-.3.7-.4 1-.2 1.1.4 2.3.6 3.6.6.6 0 1 .4 1 1V20c0 .6-.4 1-1 1C10.6 21 3 13.4 3 4c0-.6.4-1 1-1h3.5c.6 0 1 .4 1 1 0 1.3.2 2.5.6 3.6.1.3 0 .7-.2 1l-2.3 2.2z"/></svg>
      <span>(210) 555-0147</span>
    </div>
    <div class="company-address">
      <div class="company-name">Brightwick Gadget Clinic LLC</div>
      <div>4810 E Harlow Ridge Rd</div>
      <div>Suite 417 San Antonio, TX 78163</div>
    </div>
    <div class="brand-panel">
      <span class="brand-square"></span>
      <span class="brand-name">Brightwick Gadget Clinic</span>
    </div>
  </div>
</body>
</html>
```